Dental office stationary (letterhead, envelopes), business cards, presentation folders

Nothing too dental outside of the logo. I will need all stationary, presentation folders, business cards. Would prefer to stay in the colors of the logo

Gordon Patel, DDS
Bright Haven Dental Implant Center
555-318-2790
info@brighthavendental.example
4817 NW Maple Crest Rd Unit B
Lakeview, ST 00000

Also need appointment date and time
And cancellation policy
I want it to say “kindly ask for
A 48hr cancellation policy to avoid incurring a cancellation fee”

Industry/Entity Type

Dental

Colors
0054AA
0677BA
7BADD7
CADEEF
E8F1F8

Requirements
Must have
• Name of your office, name of doctor, address, phone number
Should not have
• Too much tooth/dental. Only the tooth in logo

```html
<!DOCTYPE html>
<html lang="en">
<head>
<meta charset="utf-8">
<title>Bright Haven Dental Implant Center – Stationery Set</title>
<link rel="stylesheet" href="https://fonts.googleapis.com/css2?family=Arimo:wght@400;700&family=Tinos:wght@400;700&display=swap">
<style>
  :root{
    --stage:#3b3b3d;
    --teal:#1bbb9c;
    --blue:#0677ba;
    --blue-light:#1b8fd6;
    --navy:#0054aa;
    --sky:#7badd7;
    --paper:#f6f4f5;
    --white:#ffffff;
    --ink:#4a4a4a;
    --ink-soft:#7a7a7a;
  }
  *{box-sizing:border-box;margin:0;padding:0}
  html,body{width:1200px;height:292px;overflow:hidden}
  body{background:var(--stage);font-family:"Arimo",Arial,sans-serif;color:var(--ink);position:relative}
  .piece{position:absolute;overflow:hidden}
  .piece svg.shape{position:absolute;inset:0;width:100%;height:100%}

  /* brand lockup */
  .brand{position:absolute;text-align:center;font-family:"Tinos",Georgia,serif;font-weight:400;color:var(--navy);line-height:1;white-space:nowrap}
  .brand-name{display:block;letter-spacing:.04em}
  .brand-sub{display:block;letter-spacing:.28em}

  /* business card front */
  .card-front{left:25px;top:26px;width:125px;height:71px;background:var(--white);border-radius:4px}
  .card-front .brand{left:0;right:0;top:25px}
  .card-front .brand-name{font-size:10px}
  .card-front .brand-sub{font-size:2.6px;margin-top:1.5px}
  .card-front .doctor{position:absolute;right:60px;top:47px;text-align:right;white-space:nowrap}
  .doctor-name{font-family:"Tinos",Georgia,serif;font-size:5px;color:var(--navy);font-weight:700;letter-spacing:.02em}
  .doctor-title{font-size:2.8px;color:var(--blue)}
  .doctor-mail{font-size:2.8px;color:var(--ink)}
  .card-front .contact{position:absolute;left:69px;top:46px;border-left:.4px solid var(--ink-soft);padding-left:2px;font-size:2.8px;line-height:1.45;color:var(--ink);white-space:nowrap}

  /* business card back */
  .card-back{left:22px;top:110px;width:128px;height:73px;border-radius:4px;background:radial-gradient(circle at 55% 45%,var(--blue-light),var(--blue) 75%)}
  .card-back .brand{left:0;right:0;top:31px;color:var(--navy)}
  .card-back .brand-name{font-size:11.5px}
  .card-back .brand-sub{font-size:3px;margin-top:1.5px}

  /* appointment card */
  .appt-card{left:22px;top:199px;width:128px;height:72px;background:var(--white);border-radius:3px}
  .appt-title{position:absolute;left:0;right:0;top:8px;text-align:center;font-size:5px;color:var(--blue)}
  .appt-rows{position:absolute;left:7px;right:7px;top:19px}
  .appt-row{display:flex;align-items:baseline;height:8.2px;font-size:3.8px;color:var(--blue)}
  .appt-row .dots{flex:1;border-bottom:.5px dotted var(--ink-soft);margin:0 1px}
  .appt-row .ampm{font-size:2.6px}
  .appt-band{position:absolute;left:0;right:0;top:56px;height:6px;background:var(--blue);color:var(--white);font-size:3.4px;letter-spacing:.18em;text-align:center;line-height:6px}
  .appt-policy{position:absolute;left:0;right:0;top:64.5px;font-size:2.8px;text-align:center;color:var(--ink)}

  /* letterhead */
  .letterhead{left:170px;top:26px;width:175px;height:246px;background:var(--paper)}
  .letterhead .brand{left:17px;top:11px;color:var(--white)}
  .letterhead .brand-name{font-size:6.5px}
  .letterhead .brand-sub{font-size:1.6px;margin-top:1px}
  .lh-address{position:absolute;right:62px;top:12px;text-align:right;color:var(--white);font-size:2.4px;line-height:1.4;white-space:nowrap}
  .lh-reach{position:absolute;left:118px;top:12px;border-left:.4px solid var(--white);padding-left:2px;color:var(--white);font-size:2.4px;line-height:1.4;white-space:nowrap}
  .lh-body{position:absolute;left:17px;right:17px;top:62px}
  .salutation{font-size:4.6px;color:var(--ink);margin-bottom:7px}
  .lh-body p{font-size:2.5px;line-height:1.65;color:var(--ink-soft);text-align:justify;margin-bottom:4px}
  .signoff{font-size:2.6px;color:var(--ink-soft);margin-top:6px}
  .signer{margin-top:16px;font-size:3.2px;color:var(--ink)}
  .signer-role{font-size:2.5px;color:var(--ink-soft)}
  .lh-web{position:absolute;left:0;right:0;bottom:3px;text-align:center;font-size:2.5px;color:var(--ink-soft)}

  /* envelopes */
  .envelope-back{left:367px;top:53px;width:196px;height:89px;background:var(--paper)}
  .envelope-back .brand{left:0;right:0;top:16px;color:var(--white)}
  .envelope-back .brand-name{font-size:8.5px}
  .envelope-back .brand-sub{font-size:2px;margin-top:1px}
  .envelope-front{left:366px;top:162px;width:197px;height:89px;background:var(--paper)}
  .envelope-front .brand{left:12px;top:12px;color:var(--white)}
  .envelope-front .brand-name{font-size:6.8px}
  .envelope-front .brand-sub{font-size:1.7px;margin-top:1px}
  .env-contact{position:absolute;left:12px;top:58px;font-size:2.6px;line-height:1.45;color:var(--ink);white-space:nowrap}

  .ico{display:inline-block;width:2.2px;height:2.2px;border-radius:50%;background:var(--blue);margin-right:1.5px;vertical-align:middle}

  /* closed folder */
  .folder-closed{left:580px;top:61px;width:292px;height:183px}
  .folder-back{position:absolute;left:0;top:0;width:146px;height:183px;background:radial-gradient(circle at 45% 35%,var(--blue-light),var(--blue) 80%)}
  .folder-back .contact{position:absolute;left:12px;top:153px;font-size:3px;line-height:1.45;color:var(--white);white-space:nowrap}
  .folder-back .contact .ico{background:var(--white)}
  .folder-back .web{position:absolute;right:10px;top:168px;font-size:3px;color:var(--white)}
  .folder-front{position:absolute;left:146px;top:0;width:146px;height:183px;background:var(--white)}
  .folder-front .brand{left:0;right:0;top:88px}
  .folder-front .brand-name{font-size:15px}
  .folder-front .brand-sub{font-size:3.6px;margin-top:2px}

  /* open folder */
  .folder-open{left:883px;top:62px;width:291px;height:184px}
  .folder-open .brand{top:146px;color:var(--white)}
  .folder-open .brand-name{font-size:12.5px}
  .folder-open .brand-sub{font-size:3.2px;margin-top:2px}
  .pocket-left{left:0;width:136px}
  .pocket-right{left:157px;width:134px}
</style>
</head>
<body>

<section class="piece card-front" aria-label="Business card front">
  <svg class="shape" viewBox="0 0 125 71" preserveAspectRatio="none">
    <path d="M0 0H125V20Q62 4 0 23Z" fill="var(--teal)"/>
    <path d="M0 23Q62 4 125 20" fill="none" stroke="var(--navy)" stroke-width="1"/>
  </svg>
  <div class="brand">
    <span class="brand-name">BRIGHT HAVEN</span>
    <span class="brand-sub">DENTAL IMPLANT CENTER</span>
  </div>
  <div class="doctor">
    <div class="doctor-name">GORDON PATEL</div>
    <div class="doctor-title">DDS</div>
    <div class="doctor-mail">info@brighthavendental.example</div>
  </div>
  <div class="contact">
    4817 NW Maple Crest Rd Unit B<br>Lakeview, ST 00000<br>
    <span class="ico"></span>555-318-2790<br>
    <span class="ico"></span>www.brighthavendental.example
  </div>
</section>

<section class="piece card-back" aria-label="Business card back">
  <div class="brand">
    <span class="brand-name">BRIGHT HAVEN</span>
    <span class="brand-sub">DENTAL IMPLANT CENTER</span>
  </div>
</section>

<section class="piece appt-card" aria-label="Appointment card">
  <div class="appt-title">Next Appointment</div>
  <div class="appt-rows">
    <div class="appt-row">Date :<span class="dots"></span>Time :<span class="dots"></span><span class="ampm">AM/PM</span></div>
    <div class="appt-row">Date :<span class="dots"></span>Time :<span class="dots"></span><span class="ampm">AM/PM</span></div>
    <div class="appt-row">Date :<span class="dots"></span>Time :<span class="dots"></span><span class="ampm">AM/PM</span></div>
    <div class="appt-row">Date :<span class="dots"></span>Time :<span class="dots"></span><span class="ampm">AM/PM</span></div>
  </div>
  <div class="appt-band">www.brighthavendental.example</div>
  <div class="appt-policy">kindly ask for A 48hr cancellation policy to avoid incurring a cancellation fee</div>
</section>

<section class="piece letterhead" aria-label="Letterhead">
  <svg class="shape" viewBox="0 0 175 246" preserveAspectRatio="none">
    <path d="M0 0H175V36Q88 26 0 36Z" fill="var(--teal)"/>
    <path d="M0 37Q88 27 175 37" fill="none" stroke="var(--navy)" stroke-width=".6"/>
  </svg>
  <div class="brand">
    <span class="brand-name">BRIGHT HAVEN</span>
    <span class="brand-sub">DENTAL IMPLANT CENTER</span>
  </div>
  <div class="lh-address">4817 NW Maple Crest Rd Unit B<br>Lakeview, ST 00000</div>
  <div class="lh-reach">555-318-2790<br>info@brighthavendental.example</div>
  <div class="lh-body">
    <div class="salutation">Dear Mr. Lane,</div>
    <p>We are pleased to welcome you to our practice and look forward to caring for your smile in the months ahead. Our team will review your full treatment plan with you at your first visit, explain each step of the process in plain terms and answer any questions you may have. We want you to feel informed, calm and confident about every part of your care from the very first day.</p>
    <p>Please arrive ten minutes early to complete your patient forms. Bring a list of your current medications, your insurance card and any recent x-rays from your previous dentist so that we can plan your care in full detail. If you have special needs or concerns, let our front desk know ahead of time and we will gladly prepare for them before you arrive.</p>
    <p>Our office offers flexible scheduling, early morning visits and several payment options to suit your budget. If you need to change or cancel your appointment, please call us as early as possible so that we can offer the time to another patient who is waiting. We kindly ask for at least forty-eight hours of notice to avoid a cancellation fee. Reminders are sent by text and email two days before each visit.</p>
    <p>Thank you for choosing our center for your implant care. We value the trust you place in us and will do our very best to make each visit comfortable, relaxed and easy for you and for your family. We look forward to meeting you soon and to helping you enjoy a healthy, lasting smile.</p>
    <div class="signoff">Sincerely,</div>
    <div class="signer">Alex Rivera</div>
    <div class="signer-role">CEO/ Founder</div>
  </div>
  <div class="lh-web">www.brighthavendental.example</div>
</section>

<section class="piece envelope-back" aria-label="Envelope back">
  <svg class="shape" viewBox="0 0 196 89" preserveAspectRatio="none">
    <path d="M0 0H196L190 26Q188 32 180 32H16Q8 32 6 26Z" fill="var(--blue)"/>
  </svg>
  <div class="brand">
    <span class="brand-name">BRIGHT HAVEN</span>
    <span class="brand-sub">DENTAL IMPLANT CENTER</span>
  </div>
</section>

<section class="piece envelope-front" aria-label="Envelope front">
  <svg class="shape" viewBox="0 0 197 89" preserveAspectRatio="none">
    <path d="M0 0H197V31Q100 17 0 30Z" fill="var(--teal)"/>
    <path d="M0 31Q100 18 197 32" fill="none" stroke="var(--navy)" stroke-width=".6"/>
  </svg>
  <div class="brand">
    <span class="brand-name">BRIGHT HAVEN</span>
    <span class="brand-sub">DENTAL IMPLANT CENTER</span>
  </div>
  <div class="env-contact">
    4817 NW Maple Crest Rd Unit B<br>Lakeview, ST 00000<br>
    <span class="ico"></span>555-318-2790<br>
    <span class="ico"></span>info@brighthavendental.example<br>
    <span class="ico"></span>www.brighthavendental.example
  </div>
</section>

<section class="piece folder-closed" aria-label="Presentation folder, outside">
  <div class="folder-back">
    <div class="contact">
      4817 NW Maple Crest Rd Unit B<br>Lakeview, ST 00000<br>
      <span class="ico"></span>555-318-2790<br>
      <span class="ico"></span>info@brighthavendental.example
    </div>
    <div class="web">www.brighthavendental.example</div>
  </div>
  <div class="folder-front">
    <svg class="shape" viewBox="0 0 146 183" preserveAspectRatio="none">
      <path d="M0 0H146V31Q73 22 0 27Z" fill="var(--teal)"/>
      <path d="M0 28Q73 22 146 32" fill="none" stroke="var(--navy)" stroke-width=".8"/>
    </svg>
    <div class="brand">
      <span class="brand-name">BRIGHT HAVEN</span>
      <span class="brand-sub">DENTAL IMPLANT CENTER</span>
    </div>
  </div>
</section>

<section class="piece folder-open" aria-label="Presentation folder, inside">
  <svg class="shape" viewBox="0 0 291 184" preserveAspectRatio="none">
    <defs>
      <linearGradient id="inner-left" x1="0" x2="1">
        <stop offset="0" stop-color="#ffffff"/><stop offset="1" stop-color="#dedede"/>
      </linearGradient>
      <linearGradient id="inner-right" x1="0" x2="1">
        <stop offset="0" stop-color="#e4e4e4"/><stop offset="1" stop-color="#ffffff"/>
      </linearGradient>
    </defs>
    <rect x="0" y="0" width="146" height="184" fill="url(#inner-left)"/>
    <rect x="146" y="0" width="145" height="184" fill="url(#inner-right)"/>
    <path d="M0 110H130Q136 110 137 118L146 184H0Z" fill="var(--blue)"/>
    <path d="M165 110H291V184H155L159 118Q160 110 165 110Z" fill="var(--blue)"/>
  </svg>
  <div class="brand pocket-left">
    <span class="brand-name">BRIGHT HAVEN</span>
    <span class="brand-sub">DENTAL IMPLANT CENTER</span>
  </div>
  <div class="brand pocket-right">
    <span class="brand-name">BRIGHT HAVEN</span>
    <span class="brand-sub">DENTAL IMPLANT CENTER</span>
  </div>
</section>

</body>
</html>
```